Animal Eye Clinic needs a Business card

We are a new veterinary ophthalmology practice (Ridgeline Pet Vision Care) and we need a business card designed. We only see animal eyes - we are not a regular veterinary clinic. We already have a logo. We are looking for a professional, good looking business card to hand out to our clients. We are looking for something simple but professional and contemporary. Our logo is likely the only picture/graphic that needs to be on the card.
Updates

Contact Information for Business Card

Delia Vossman, BSc, DVM, MSc, DipACVO
Veterinary Ophthalmologist

Phone: 250.418.3927
Email: ridgelinepetvisioncare@mailbox-example.net
Website: ridgelinepetvisioncare-example.net
Address: 1874 Thornbury Rd
Kelowna, BC, V1X 4M9

Colors

Designer to choose colors to be used in the design.

Requirements
Must have
• Our logo (attached)

```html
<!DOCTYPE html>
<html lang="en">
<head>
<meta charset="utf-8">
<title>Ridgeline Pet Vision Care – Business Card</title>
<link rel="stylesheet" href="https://fonts.googleapis.com/css2?family=Open+Sans:wght@300;400;600;700&display=swap">
<style>
  :root {
    --teal: #0097a7;
    --slate: #767676;
    --ink: #4a4a4a;
    --paper: #ffffff;
    --backdrop: #d9d9db;
    --rule: #8a8a8a;
  }
  * { box-sizing: border-box; margin: 0; padding: 0; }
  html, body { width: 1200px; height: 800px; overflow: hidden; }
  body {
    background: var(--backdrop);
    font-family: "Open Sans", Arial, sans-serif;
    display: flex;
    align-items: center;
    justify-content: center;
    gap: 40px;
  }
  .card {
    position: relative;
    width: 560px;
    height: 320px;
    overflow: hidden;
    box-shadow: 0 6px 18px rgba(0,0,0,0.18);
  }

  /* Front */
  .card-front { background: var(--paper); color: var(--ink); }
  .brand {
    position: absolute;
    top: 58px;
    left: 0; right: 0;
    display: flex;
    align-items: center;
    justify-content: center;
    gap: 12px;
  }
  .brand-dot {
    width: 34px; height: 34px;
    border-radius: 50%;
    background: var(--teal);
  }
  .brand-name {
    color: var(--teal);
    font-weight: 600;
    font-size: 22px;
    line-height: 1.05;
  }
  .holder {
    position: absolute;
    left: 34px;
    top: 172px;
  }
  .holder-name {
    color: var(--teal);
    font-weight: 700;
    font-size: 18px;
  }
  .holder-creds {
    font-weight: 400;
    font-size: 12px;
  }
  .holder-title {
    font-size: 14px;
    color: var(--ink);
    margin-top: 2px;
  }
  .address {
    position: absolute;
    right: 34px;
    top: 178px;
    text-align: right;
    font-size: 13px;
    line-height: 1.45;
  }
  .divider {
    position: absolute;
    left: 34px; right: 34px;
    top: 228px;
    border-top: 1px solid var(--rule);
  }
  .contacts {
    position: absolute;
    left: 34px;
    top: 238px;
    list-style: none;
    font-size: 12.5px;
    line-height: 1.7;
  }
  .contacts li { display: flex; align-items: center; gap: 8px; }
  .contact-icon { width: 12px; height: 12px; fill: var(--teal); flex: none; }

  /* Back */
  .card-back { background: var(--slate); color: var(--paper); }
  .back-circle {
    position: absolute;
    width: 300px; height: 300px;
    left: -30px; top: 90px;
    border-radius: 50%;
    background: var(--teal);
  }
  .back-brand {
    position: absolute;
    right: 36px;
    top: 150px;
    text-align: left;
  }
  .back-brand-name {
    color: var(--teal);
    font-weight: 600;
    font-size: 28px;
    line-height: 1.05;
  }
  .back-web {
    margin-top: 8px;
    font-size: 13px;
    letter-spacing: 0.5px;
    color: var(--paper);
  }
</style>
</head>
<body>

  <section class="card card-front" aria-label="Business card front">
    <div class="brand">
      <span class="brand-dot"></span>
      <div class="brand-name">Ridgeline<br>Pet Vision Care</div>
    </div>

    <div class="holder">
      <p class="holder-name">Delia Vossman, <span class="holder-creds">BSc, DVM, MSc, DipACVO</span></p>
      <p class="holder-title">Veterinary Ophthalmologist</p>
    </div>

    <address class="address" style="font-style:normal">
      1874 Thornbury Rd<br>
      Kelowna, BC, V1X 4M9
    </address>

    <div class="divider"></div>

    <ul class="contacts">
      <li>
        <svg class="contact-icon" viewBox="0 0 24 24" aria-hidden="true"><path d="M6.6 10.8a15.1 15.1 0 0 0 6.6 6.6l2.2-2.2a1 1 0 0 1 1-.25 11.4 11.4 0 0 0 3.6.57 1 1 0 0 1 1 1V20a1 1 0 0 1-1 1A17 17 0 0 1 3 4a1 1 0 0 1 1-1h3.5a1 1 0 0 1 1 1c0 1.25.2 2.45.57 3.57a1 1 0 0 1-.25 1z"/></svg>
        250.418.3927
      </li>
      <li>
        <svg class="contact-icon" viewBox="0 0 24 24" aria-hidden="true"><path d="M2 5h20v14H2z M4 7v.5l8 5 8-5V7l-8 5z" fill-rule="evenodd"/></svg>
        ridgelinepetvisioncare@mailbox-example.net
      </li>
      <li>
        <svg class="contact-icon" viewBox="0 0 24 24" aria-hidden="true"><circle cx="12" cy="12" r="10" fill="none" stroke="currentColor" stroke-width="0"/><path d="M12 2a10 10 0 1 0 0 20 10 10 0 0 0 0-20zm0 2c.9 1.2 1.6 2.8 1.9 5h-3.8c.3-2.2 1-3.8 1.9-5zM4.3 13h3.8c.1 1.8.4 3.4 1 4.7A8 8 0 0 1 4.3 13zm0-2a8 8 0 0 1 4.8-4.7c-.6 1.3-.9 2.9-1 4.7zm5.8 2h3.8c-.2 2.3-.9 4-1.9 5-1-1-1.7-2.7-1.9-5zm0-2c.2-.1 0 0 0 0zm5.8 2h3.8a8 8 0 0 1-4.8 4.7c.6-1.3.9-2.9 1-4.7zm0-2c-.1-1.8-.4-3.4-1-4.7a8 8 0 0 1 4.8 4.7z"/></svg>
        ridgelinepetvisioncare-example.net
      </li>
    </ul>
  </section>

  <section class="card card-back" aria-label="Business card back">
    <div class="back-circle"></div>
    <div class="back-brand">
      <div class="back-brand-name">Ridgeline<br>Pet Vision Care</div>
      <p class="back-web">www.ridgelinepetvisioncare-example.net</p>
    </div>
  </section>

</body>
</html>
```